Nitrogen generation business website

Project Overview:
This project aims to create a sleek, user-friendly, and responsive WordPress template for Flo7K3, a provider of Nitrogen generation solutions. The site will serve as a primary touchpoint for customers and businesses looking to enquire about or purchase Flo7K3 products and services. The website should clearly communicate the benefits of working with Flo7K3 as a distributor, focusing on ease of access, expert consultation, and fast, reliable service.
Target Audience:
• Industrial companies seeking Nitrogen solutions.
• Engineers, facility managers, and purchasing teams in need of high-quality Nitrogen systems.
• Partners or businesses seeking to collaborate or purchase through a distributor.
Key Objectives:
1. Establish Flo7K3’s Brand Identity: Use the bold, energetic logo and branding of Flo7K3 (as seen in the uploaded logo) throughout the design. Ensure the brand’s personality shines, with a focus on modernity, reliability, and innovation.
2. Showcase Products and Solutions: Display detailed product categories and descriptions, emphasising the solutions Flo7K3 offers.
3. Lead Generation: Incorporate contact forms, quote requests, and easy-to-find CTAs to convert visitors into leads.
4. User-Centric Design: The design must be intuitive and user-friendly, providing a smooth experience across desktop and mobile devices.
Design Requirements:
1. Home Page:
• Hero Banner: A dynamic, visually engaging hero banner featuring air and gas purification systems, paired with strong CTAs like “Request a Quote” or “Contact Us for Solutions.” The banner should align with the vibrant red and yellow tones in the Flo7K3 logo.
• Key Product Categories: Introduce the main product categories with icons or images linked to individual product pages.
• Flo7K3 Expertise Section: A section emphasising the company’s role as a trusted distributor, backed by experience and a strong partnership network.
• Why Choose Flo7K3: Highlight 3-4 major benefits, such as “Quick Delivery,” “Expert Consultation,” and “Innovative Technology.”
• Client Testimonials/Partners: Space for customer feedback, testimonials, or logos of partner companies to build trust.
• Newsletter or Enquiry Form: Place a compact form for capturing visitor details for quotes, enquiries, or subscriptions.
2. Product Pages:
• Category Pages: Create well-structured product category pages (e.g., Air Filtration Systems, Nitrogen Generators) similar to industry-standard designs. Each category page should feature professional imagery, short product descriptions, and links to detail pages.
• Product Detail Pages: Each product page will contain:
• High-quality images of the product.
• Detailed specifications, technical descriptions, and features.
• Options to download datasheets or brochures (PDF format).
• Clear CTAs to request a quote or contact sales.
• Product Comparison Tool (Optional): Allow users to compare multiple products, emphasising key features and specifications.
3. About Flo7K3 Page:
• Provide an overview of Flo7K3’s history, mission, and the value it provides as a leading distributor.
• Highlight industry expertise, the partnership network, and any accolades or certifications.
• Mention any regional advantages or special services (e.g., fast delivery times, on-site consultation).
4. Contact Us Page:
• Clean and Simple Form: Include fields for general inquiries or specific product requests.
• Contact Information: Display the company’s, email address info@flo7k3.co.uk.
5. Additional Functionalities:
• Responsive Design: Ensure the design is fully responsive, optimised for mobile, tablet, and desktop viewing.
• SEO Optimisation: Include best practices for search engine optimization (SEO), including clean URLs, meta tags, and image alt text.
• Fast Loading Speed: Optimise images, scripts, and code for fast loading times to improve user experience.
• Social Media Integration: Provide links to social media profiles (if applicable) and potentially include a feed for recent updates.
• Optional Blog: Create a blog space for sharing industry news, product updates, or educational content to engage with visitors and improve SEO.
Style Guide:
1. Color Palette:
• Use colors consistent with the Flo7K3 logo: Red (#FF0000) and Yellow (#FFD700) as primary colors. Incorporate neutral colors (such as white, gray, or black) for balance and readability.
• Accent colors may be introduced for subtle highlights, but the focus should be on the bold, energetic color scheme of Flo7K3.
2. Typography:
• Primary Font for Headings: A bold, modern sans-serif font that complements the strong branding of Flo7K3.
• Secondary Font for Body Text: Clean, easy-to-read sans-serif or serif font for optimal readability across devices.
• Typography Emphasis: Use large, bold typography for headlines to match the boldness of the logo and brand identity.
3. Imagery:
• Use high-quality industrial and technical imagery that reflects the air and gas purification products Flo7K3 distributes.
• Incorporate imagery showing products in action, e.g., in industrial settings or installations.
• Avoid clutter; ensure images are used to enhance user understanding, not overwhelm.
4. Icons:
• Utilise modern, flat-style icons that align with the clean and professional image of Flo7K3. Icons could represent services such as “Fast Delivery,” “Expert Support,” and “High-Quality Products.”
Functionality Requirements:
1. Content Management System (CMS): Build the site using WordPress for easy content management, allowing Flo7K3 staff to update content, product information, and blog posts.
2. Quote Request Integration: Ensure the site has a functional and easy-to-access “Request a Quote” form that appears on every product and service page.
3. Customer Support Section: Optionally include a section for FAQs, product guides, or a knowledge base to support customers and prospects.
4. Security: Implement SSL encryption and ensure that other security best practices (e.g., spam prevention for forms) are followed.
5. Multilingual Support (Optional): Provide the option to support multiple languages, depending on the regional scope of Flo7K3’s distribution services.
Deliverables:
• WordPress template with a homepage, product pages, about section, and contact page.
• SEO-friendly and responsive design.
• Clear CTAs for lead generation (e.g., “Request a Quote”).
• User-friendly interface for both desktop and mobile devices.
Inspiration/Competitors:
• Competitor Analysis: Research similar distributors in the air and gas purification industry for design inspiration.
• Brand Consistency: Ensure Flo7K3’s bold branding is prominent and differentiates it from competitors.
Target Market(s)
Food & Beverage manufacturers, Laser Cutting, Electronics manufacturers, General Industrial Manufacturers

```html
<!DOCTYPE html>
<html lang="en">
<head>
<meta charset="utf-8">
<title>Flo7K3 — Nitrogen Generation Website Pages</title>
<link rel="stylesheet" href="https://fonts.googleapis.com/css2?family=Lexend:wght@400;500;600;700&family=Montserrat:wght@400;500;600;700&display=swap">
<style>
:root{
  --yellow:#FFC400;
  --red:#FF2A1E;
  --ink:#1B1B1B;
  --muted:#5A4A1A;
  --board:#E6E6E6;
  --white:#FFFFFF;
  --line:#F0A8A4;
  --photo-warm:linear-gradient(135deg,#3a4a52,#c89a3a 60%,#e7b73a);
  --photo-steel:linear-gradient(160deg,#f2f2f2,#9aa0a6 55%,#2a2a2a);
}
*{box-sizing:border-box;margin:0;padding:0}
html,body{width:1200px;height:1200px;overflow:hidden;background:var(--board)}
body{font-family:"Montserrat",sans-serif;color:var(--ink)}
.board{position:absolute;left:0;top:0;width:1932px;height:1932px;transform:scale(0.62112);transform-origin:0 0;background:var(--board)}
.page{position:absolute;background:var(--white);overflow:hidden}
.abs{position:absolute}
h1,h2,h3,.brand{font-family:"Lexend",sans-serif;font-weight:500}
.brand{color:var(--red);font-weight:700;font-size:17px;letter-spacing:.2px;display:flex;align-items:center;gap:4px}
.brand .dot{width:6px;height:6px;border-radius:50%;background:var(--yellow)}
.nav-links{display:flex;gap:9px;font-size:4px;font-weight:600;letter-spacing:.2px}
.nav-links .on{color:var(--red)}
.nav-icons{display:flex;gap:9px;align-items:center}
.nav-icons svg{width:8px;height:8px}
.btn{position:absolute;background:var(--red);color:var(--white);font-size:7px;font-weight:600;display:flex;align-items:center;justify-content:center;border-radius:3px}
.photo{position:absolute;border-radius:6px}
.prod{position:absolute;background:var(--photo-steel);border-radius:4px}
.dots{position:absolute;display:flex;gap:4px}
.dots i{width:5px;height:5px;border-radius:50%;border:1px solid var(--red)}
.dots i:first-child{background:var(--red)}
.icon-box{position:absolute;width:58px;height:58px;border-radius:5px;display:flex;align-items:center;justify-content:center}
.icon-box svg{width:30px;height:30px}
.cat-label{position:absolute;font-size:7px;text-align:center;width:70px;line-height:1.3;color:#444}
.checks{display:grid;grid-template-columns:1fr 1fr;gap:10px 12px}
.check{display:flex;gap:5px;font-size:7px;line-height:1.25;color:#333}
.check svg{width:8px;height:8px;flex:none}
.why-card{position:absolute;width:123px;height:116px;border-radius:5px;padding:14px 14px}
.why-card .ic{width:34px;height:34px;border-radius:4px;margin-bottom:12px}
.why-card h4{font-size:7px;font-weight:700;line-height:1.3;margin-bottom:4px}
.why-card p{font-size:3.2px;line-height:1.4}
.testi{position:absolute;background:var(--red);color:var(--white);text-align:center}
.testi h2{font-size:16px;font-weight:400}
.quote{color:var(--yellow);font-family:"Lexend",sans-serif;font-size:44px;font-weight:700;line-height:1}
.avatar{position:absolute;border-radius:50%;background:linear-gradient(135deg,#c9a27a,#5a3a2a)}
.news{position:absolute;background:var(--yellow);border-radius:6px}
.news h3{font-size:15px;font-weight:600;line-height:1.25}
.news p{font-size:6.5px;line-height:1.4;color:#3a2f00}
.sub-form{position:absolute;display:flex;height:26px;border-radius:4px;overflow:hidden}
.sub-form span{flex:1;background:var(--white);font-size:6px;color:#999;display:flex;align-items:center;padding-left:18px}
.sub-form b{background:var(--red);color:var(--white);font-size:6.5px;font-weight:600;display:flex;align-items:center;padding:0 12px}
.footer{position:absolute;background:var(--yellow);border-top-left-radius:50px}
.footer .brand{position:absolute;font-size:18px}
.footer .about{position:absolute;font-size:4px;line-height:1.35;width:70px;color:#4a3a00}
.fcol{position:absolute;font-size:4px;color:#4a3a00;line-height:1.35}
.fcol h5{font-size:6.5px;font-weight:700;color:var(--ink);margin-bottom:14px}
.fcol .row{display:flex;gap:8px;margin-bottom:11px;align-items:flex-start}
.fcol .row svg{width:8px;height:8px;flex:none}
.fcol .lnk{margin-bottom:11px}
.socials{display:flex;gap:11px;margin-top:14px}
.socials i{width:12px;height:12px;border-radius:50%;background:var(--red)}
.p-card{position:absolute;width:188px;height:100px;border-radius:6px;overflow:hidden}
.p-card h4{position:absolute;left:14px;top:16px;font-family:"Lexend",sans-serif;font-weight:400;font-size:11px;line-height:1.25}
.p-card .btn{left:14px;top:70px;width:51px;height:14px;font-size:4.5px;font-weight:500}
.p-card .blob{position:absolute;border-top-left-radius:26px}
.acc{position:absolute;left:54px;width:405px;border-top:1px solid var(--line);font-size:8px;font-weight:700}
.acc .r{display:flex;justify-content:space-between;align-items:center;padding:0 10px;height:32px;border-bottom:1px solid var(--line)}
.acc svg{width:6px;height:6px}
.spec{position:absolute;left:54px;width:405px;font-size:8px}
.spec .r{display:flex;justify-content:space-between;align-items:center;padding:0 7px 0 10px;height:32px;border-bottom:1px solid var(--line)}
.spec .r b{font-weight:700}
.cmp{position:absolute;left:54px;width:406px;font-size:8px}
.cmp .h{display:grid;grid-template-columns:142px 142px 1fr;background:var(--yellow);border-radius:5px;height:33px;align-items:center;padding-left:10px;font-weight:700;line-height:1.2}
.cmp .r{display:grid;grid-template-columns:136px 153px 1fr;border-bottom:1px solid var(--line);align-items:end;padding:0 0 4px 6px;min-height:26.5px;line-height:1.2}
.radio{position:absolute;left:54px;display:flex;gap:14px;align-items:center;font-size:8px;font-weight:700}
.radio i{width:11px;height:11px;border-radius:50%;border:2.5px solid var(--red);background:var(--white);box-shadow:inset 0 0 0 2px #fff,inset 0 0 0 5px var(--red)}
</style>
</head>
<body>
<div class="board">

<!-- ===== Desktop home ===== -->
<section class="page" style="left:66px;top:115px;width:480px;height:1612px">
  <div class="brand abs" style="left:50px;top:15px">Flo7K3<span class="dot"></span></div>
  <nav class="nav-links abs" style="left:192px;top:23px"><span class="on">HOME</span><span>PRODUCT</span><span>ABOUT US</span><span>SERVICES</span><span>BLOG</span><span>CONTACT US</span></nav>
  <div class="nav-icons abs" style="left:389px;top:21px">
    <svg viewBox="0 0 10 10" fill="none" stroke="#333" stroke-width="1"><circle cx="5" cy="3.2" r="2"/><path d="M1.5 9.5c.5-2.5 6.5-2.5 7 0"/></svg>
    <svg viewBox="0 0 10 10" fill="none" stroke="#333" stroke-width="1"><rect x="1.5" y="3" width="7" height="6" rx="1"/><path d="M3.5 3V2h3v1"/></svg>
    <span style="font-size:3px">GBP</span>
  </div>

  <div class="abs" style="left:0;top:46px;width:480px;height:254px;background:var(--yellow);border-bottom-left-radius:50px"></div>
  <div class="abs" style="left:223px;top:123px;width:257px;height:177px;background:var(--red);border-top-left-radius:80px"></div>
  <h1 class="abs" style="left:50px;top:60px;font-size:24px;font-weight:400;line-height:1.18;letter-spacing:.3px">Enhance Your Operations<br>with Reliable Nitrogen Solutions</h1>
  <p class="abs" style="left:50px;top:153px;font-size:7px;line-height:1.3;width:160px">Discover How Our Advanced Nitrogen Generators Can Optimise Your Business</p>
  <div class="btn" style="left:50px;top:212px;width:92px;height:28px">Request a Quote</div>
  <div class="prod" role="img" aria-label="Two modular nitrogen generator units" style="left:300px;top:128px;width:112px;height:165px"></div>
  <div class="dots" style="left:50px;top:278px"><i></i><i></i><i></i></div>

  <h2 class="abs" style="left:50px;top:336px;font-size:15px;line-height:1.25">Explore Our<br>Solutions</h2>
  <p class="abs" style="left:50px;top:388px;font-size:7px;line-height:1.3;width:130px">Find the Right Nitrogen Generator for Your Needs</p>
  <div class="icon-box" style="left:244px;top:335px;background:var(--red)"><svg viewBox="0 0 30 30" fill="none" stroke="#FFC400" stroke-width="1.3"><rect x="7" y="5" width="16" height="21" rx="2"/><rect x="10" y="9" width="10" height="7"/><path d="M10 20h10M12 5V3h6v2"/></svg></div>
  <div class="icon-box" style="left:310px;top:335px;background:var(--yellow)"><svg viewBox="0 0 30 30" fill="none" stroke="#FF2A1E" stroke-width="1.3"><rect x="6" y="6" width="7" height="19" rx="3"/><rect x="17" y="6" width="7" height="19" rx="3"/><path d="M6 4h18"/></svg></div>
  <div class="icon-box" style="left:374px;top:335px;background:var(--red)"><svg viewBox="0 0 30 30" fill="none" stroke="#FFC400" stroke-width="1.3"><rect x="7" y="9" width="16" height="17" rx="2"/><path d="M11 9V5h8v4M7 14h16"/></svg></div>
  <div class="cat-label" style="left:238px;top:407px">Nitrogen<br>Generators</div>
  <div class="cat-label" style="left:304px;top:407px">Filtration<br>Systems</div>
  <div class="cat-label" style="left:368px;top:407px">Air Purification<br>Solutions</div>

  <div class="photo" role="img" aria-label="Engineer in a hard hat servicing industrial equipment" style="left:50px;top:451px;width:155px;height:209px;background:var(--photo-warm)"></div>
  <div class="abs" style="left:211px;top:451px;width:220px;height:209px;background:var(--yellow);border-radius:6px;padding:22px 25px">
    <h3 style="font-size:14px;line-height:1.3;margin-bottom:14px">Our Expertise in Advanced Nitrogen Technology</h3>
    <div class="checks">
      <div class="check"><svg viewBox="0 0 8 8" fill="none" stroke="#FF2A1E" stroke-width=".8"><rect x=".5" y=".5" width="7" height="7" rx="1.5"/><path d="M2 4l1.4 1.4L6 2.8"/></svg>Comprehensive Solutions</div>
      <div class="check"><svg viewBox="0 0 8 8" fill="none" stroke="#FF2A1E" stroke-width=".8"><rect x=".5" y=".5" width="7" height="7" rx="1.5"/><path d="M2 4l1.4 1.4L6 2.8"/></svg>Experienced Team</div>
      <div class="check"><svg viewBox="0 0 8 8" fill="none" stroke="#FF2A1E" stroke-width=".8"><rect x=".5" y=".5" width="7" height="7" rx="1.5"/><path d="M2 4l1.4 1.4L6 2.8"/></svg>Advanced Technology</div>
      <div class="check"><svg viewBox="0 0 8 8" fill="none" stroke="#FF2A1E" stroke-width=".8"><rect x=".5" y=".5" width="7" height="7" rx="1.5"/><path d="M2 4l1.4 1.4L6 2.8"/></svg>Global Partnerships</div>
    </div>
    <div class="btn" style="left:26px;top:160px;width:91px;height:25px">Contact Us</div>
  </div>

  <h2 class="abs" style="left:0;top:693px;width:482px;text-align:center;font-size:16px">Why Choose Flo7K3</h2>
  <div class="why-card" style="left:50px;top:732px;background:var(--red);color:var(--white)"><div class="ic" style="background:var(--yellow)"></div><h4>Fast and Flexible Delivery</h4><p>Streamlined logistics deliver your system fast, with flexible installation options to match your project schedule.</p></div>
  <div class="why-card" style="left:179px;top:740px;background:var(--yellow)"><div class="ic" style="background:var(--red)"></div><h4>Expert Consultation and Support</h4><p>Our experts offer tailored consultation and ongoing support to help you choose and maintain the best solution.</p></div>
  <div class="why-card" style="left:308px;top:740px;background:var(--yellow)"><div class="ic" style="background:var(--red)"></div><h4>Innovative Technology</h4><p>We stay ahead of industry trends, building the latest technology into products for reliable, cutting-edge results.</p></div>

  <div class="testi" style="left:0;top:892px;width:480px;height:256px;border-bottom-right-radius:50px;padding-top:33px">
    <h2>What Our Clients Say</h2>
    <div class="quote" style="margin-top:6px">“</div>
    <p style="font-size:7px;line-height:1.35;width:380px;margin:0 auto">We've worked with Flo7K3 for several years and have always been impressed by their professionalism and expertise. Their solutions are top-notch, and their quick delivery has been crucial for our tight schedules.</p>
    <p style="font-size:7px;font-weight:600;margin-top:11px">Maya Collins, Plant Manager, Brightline Industrial</p>
    <div class="avatar" role="img" aria-label="Client portrait" style="left:141px;top:185px;width:37px;height:37px"></div>
    <div class="avatar" role="img" aria-label="Client portrait" style="left:192px;top:182px;width:43px;height:43px;border:3px solid var(--yellow)"></div>
    <div class="avatar" role="img" aria-label="Client portrait" style="left:248px;top:185px;width:37px;height:37px"></div>
    <div class="avatar" role="img" aria-label="Client portrait" style="left:302px;top:185px;width:37px;height:37px"></div>
  </div>

  <div class="news" style="left:50px;top:1183px;width:220px;height:208px;padding:28px 24px">
    <h3>Stay Updated with<br>Flo7K3</h3>
    <p style="margin-top:30px">Join our mailing list to receive updates on new products, industry news, and exclusive offers.</p>
    <div class="sub-form" style="left:24px;top:147px;width:162px"><span>Enter your email</span><b>Subscribe</b></div>
  </div>
  <div class="photo" role="img" aria-label="Smiling engineer in yellow jacket holding a tablet" style="left:276px;top:1180px;width:156px;height:210px;background:var(--photo-warm)"></div>

  <footer class="footer" style="left:0;top:1432px;width:480px;height:180px">
    <div class="brand" style="left:50px;top:42px">Flo7K3<span class="dot"></span></div>
    <p class="about" style="left:50px;top:70px">Reliable on-site nitrogen systems, supplied and supported by a dedicated expert team.</p>
    <div class="fcol" style="left:160px;top:52px;width:80px">
      <h5>Get In Touch</h5>
      <div class="row"><svg viewBox="0 0 8 8" fill="none" stroke="#FF2A1E" stroke-width=".7"><path d="M4 7.5S1.5 5 1.5 3.2a2.5 2.5 0 015 0C6.5 5 4 7.5 4 7.5z"/><circle cx="4" cy="3.2" r=".9"/></svg>82 Harbour Lane,<br>Leeds LS1 4AB</div>
      <div class="row"><svg viewBox="0 0 8 8" fill="none" stroke="#FF2A1E" stroke-width=".7"><rect x="1" y="2" width="6" height="4.5" rx=".6"/><path d="M1 2.5l3 2 3-2"/></svg>info@flo7k3.co.uk</div>
      <div class="row"><svg viewBox="0 0 8 8" fill="none" stroke="#FF2A1E" stroke-width=".7"><path d="M2 1h1.3l.7 1.7-.9.6a4 4 0 001.6 1.6l.6-.9 1.7.7V6a1 1 0 01-1 1C3.3 7 1 4.7 1 2a1 1 0 011-1z"/></svg>(201) 555-0148<br>(702) 555-0176</div>
    </div>
    <div class="fcol" style="left:256px;top:52px"><h5>Explore Link</h5><div class="lnk">About Us</div><div class="lnk">Career</div><div class="lnk">FAQ</div><div class="lnk">Blog</div><div class="lnk">Product</div></div>
    <div class="fcol" style="left:341px;top:52px"><h5>Office Time</h5>Mon-Sat: 10:00AM - 4:00PM<br>Sunday: 10:00AM - 4:00PM<br>Friday: Close<div class="socials"><i></i><i></i><i></i></div></div>
  </footer>
</section>

<!-- ===== Mobile home ===== -->
<section class="page" style="left:582px;top:115px;width:219px;height:1618px">
  <div class="brand abs" style="left:16px;top:11px;font-size:15px">Flo7K3<span class="dot"></span></div>
  <svg class="abs" style="left:185px;top:12px;width:20px;height:13px" viewBox="0 0 20 13" stroke="#FF2A1E" stroke-width="1.5"><path d="M0 1h20M0 6.5h20M0 12h20"/></svg>
  <div class="abs" style="left:0;top:37px;width:219px;height:353px;background:var(--yellow);border-bottom-left-radius:40px"></div>
  <div class="abs" style="left:45px;top:245px;width:174px;height:145px;background:var(--red);border-top-left-radius:55px"></div>
  <h1 class="abs" style="left:16px;top:50px;font-size:17.5px;font-weight:400;line-height:1.3">Enhance Your<br>Operations<br>with Reliable<br>Nitrogen Solutions</h1>
  <p class="abs" style="left:16px;top:160px;font-size:5px;line-height:1.35;width:130px">Discover How Our Advanced Nitrogen Generators Can Optimise Your Business</p>
  <div class="btn" style="left:16px;top:199px;width:74px;height:22px;font-size:5.5px">Request a Quote</div>
  <div class="prod" role="img" aria-label="Two modular nitrogen generator units" style="left:108px;top:248px;width:82px;height:132px"></div>

  <h2 class="abs" style="left:16px;top:410px;font-size:12.5px;line-height:1.25">Explore Our<br>Solutions</h2>
  <p class="abs" style="left:16px;top:448px;font-size:5px">Find the Right Nitrogen Generator for Your Needs</p>
  <div class="icon-box" style="left:16px;top:477px;background:var(--red)"><svg viewBox="0 0 30 30" fill="none" stroke="#FFC400" stroke-width="1.3"><rect x="7" y="5" width="16" height="21" rx="2"/><rect x="10" y="9" width="10" height="7"/><path d="M10 20h10"/></svg></div>
  <div class="icon-box" style="left:81px;top:477px;background:var(--yellow)"><svg viewBox="0 0 30 30" fill="none" stroke="#FF2A1E" stroke-width="1.3"><rect x="6" y="6" width="7" height="19" rx="3"/><rect x="17" y="6" width="7" height="19" rx="3"/></svg></div>
  <div class="icon-box" style="left:146px;top:477px;background:var(--red)"><svg viewBox="0 0 30 30" fill="none" stroke="#FFC400" stroke-width="1.3"><rect x="7" y="9" width="16" height="17" rx="2"/><path d="M11 9V5h8v4"/></svg></div>
  <div class="cat-label" style="left:10px;top:548px;font-size:5px">Nitrogen<br>Generators</div>
  <div class="cat-label" style="left:75px;top:548px;font-size:5px">Filtration Systems</div>
  <div class="cat-label" style="left:140px;top:548px;font-size:5px">Air Purification<br>Solutions</div>

  <div class="photo" role="img" aria-label="Engineer in a hard hat servicing industrial equipment" style="left:16px;top:582px;width:188px;height:175px;background:var(--photo-warm)"></div>
  <div class="abs" style="left:16px;top:772px;width:188px;height:180px;background:var(--yellow);border-radius:5px;padding:20px 21px">
    <h3 style="font-size:11px;line-height:1.3;margin-bottom:12px">Our Expertise in Advanced Nitrogen Technology</h3>
    <div class="checks" style="gap:8px 6px">
      <div class="check" style="font-size:5px"><svg viewBox="0 0 8 8" fill="none" stroke="#FF2A1E" stroke-width=".8"><rect x=".5" y=".5" width="7" height="7" rx="1.5"/><path d="M2 4l1.4 1.4L6 2.8"/></svg>Comprehensive Solutions</div>
      <div class="check" style="font-size:5px"><svg viewBox="0 0 8 8" fill="none" stroke="#FF2A1E" stroke-width=".8"><rect x=".5" y=".5" width="7" height="7" rx="1.5"/><path d="M2 4l1.4 1.4L6 2.8"/></svg>Experienced Team</div>
      <div class="check" style="font-size:5px"><svg viewBox="0 0 8 8" fill="none" stroke="#FF2A1E" stroke-width=".8"><rect x=".5" y=".5" width="7" height="7" rx="1.5"/><path d="M2 4l1.4 1.4L6 2.8"/></svg>Advanced Technology</div>
      <div class="check" style="font-size:5px"><svg viewBox="0 0 8 8" fill="none" stroke="#FF2A1E" stroke-width=".8"><rect x=".5" y=".5" width="7" height="7" rx="1.5"/><path d="M2 4l1.4 1.4L6 2.8"/></svg>Global Partnerships</div>
    </div>
    <div class="btn" style="left:23px;top:137px;width:78px;height:22px;font-size:5.5px">Contact Us</div>
  </div>

  <div class="testi" style="left:0;top:966px;width:219px;height:240px;border-bottom-right-radius:36px;padding-top:27px">
    <h2 style="font-size:12px;line-height:1.25">What Our<br>Clients Say</h2>
    <div class="quote" style="font-size:34px;margin-top:4px">“</div>
    <p style="font-size:5px;line-height:1.35;width:188px;margin:0 auto">We've worked with Flo7K3 for several years and have always been impressed by their professionalism and expertise. Their solutions are top-notch, and their quick delivery has been crucial for our tight schedules.</p>
    <p style="font-size:5px;font-weight:600;margin-top:20px">Maya Collins, Plant Manager, Brightline Industrial</p>
    <div class="avatar" role="img" aria-label="Client portrait" style="left:93px;top:184px;width:34px;height:34px;border:3px solid var(--yellow)"></div>
  </div>

  <div class="photo" role="img" aria-label="Smiling engineer in yellow jacket holding a tablet" style="left:16px;top:1222px;width:188px;height:174px;background:var(--photo-warm)"></div>
  <div class="news" style="left:16px;top:1410px;width:190px;height:180px;padding:24px 20px">
    <h3 style="font-size:11.5px">Stay Updated with<br>Flo7K3</h3>
    <p style="margin-top:25px;font-size:5px">Join our mailing list to receive updates on new products, industry news, and exclusive offers.</p>
    <div class="sub-form" style="left:20px;top:128px;width:141px;height:22px"><span style="font-size:5px;padding-left:14px">Enter your email</span><b style="font-size:5.5px">Subscribe</b></div>
  </div>
</section>

<!-- ===== Product category ===== -->
<section class="page" style="left:836px;top:115px;width:482px;height:893px">
  <div class="brand abs" style="left:50px;top:25px">Flo7K3<span class="dot"></span></div>
  <nav class="nav-links abs" style="left:192px;top:31px"><span>HOME</span><span class="on">PRODUCT</span><span>ABOUT US</span><span>SERVICES</span><span>BLOG</span><span>CONTACT US</span></nav>
  <div class="nav-icons abs" style="left:390px;top:29px">
    <svg viewBox="0 0 10 10" fill="none" stroke="#333" stroke-width="1"><circle cx="5" cy="3.2" r="2"/><path d="M1.5 9.5c.5-2.5 6.5-2.5 7 0"/></svg>
    <svg viewBox="0 0 10 10" fill="none" stroke="#333" stroke-width="1"><rect x="1.5" y="3" width="7" height="6" rx="1"/></svg>
    <span style="font-size:3px">GBP</span>
  </div>
  <div class="abs" style="left:0;top:53px;width:482px;height:195px;background:var(--red);border-bottom-left-radius:60px"></div>
  <div class="abs" style="left:313px;top:118px;width:169px;height:130px;background:var(--yellow);border-top-left-radius:45px"></div>
  <h1 class="abs" style="left:47px;top:78px;font-size:22px;font-weight:400;line-height:1.25;color:var(--white)">Nitrogen<br>Generators</h1>
  <p class="abs" style="left:50px;top:143px;font-size:6.5px;line-height:1.3;width:210px;color:var(--white)">Discover our range of PSA and Membrane Nitrogen Generators designed for high efficiency and reliable on-site nitrogen production.</p>
  <div class="prod" role="img" aria-label="Large twin-tower PSA nitrogen generator skid" style="left:292px;top:63px;width:142px;height:175px"></div>
  <div class="dots" style="left:50px;top:216px"><i style="background:var(--yellow);border-color:var(--yellow)"></i><i style="border-color:var(--yellow)"></i><i style="border-color:var(--yellow)"></i></div>

  <p class="abs" style="left:50px;top:273px;font-size:7px;font-weight:500">Home &gt; <span style="color:var(--red)">Product</span></p>
  <h2 class="abs" style="left:50px;top:302px;font-size:15px;line-height:1.28;width:280px;font-weight:600">Discover Cutting-Edge Nitrogen Generation Solutions Tailored for Your Industry</h2>
  <p class="abs" style="left:50px;top:377px;font-size:6.5px;line-height:1.3;width:380px;color:#333">Flo7K3 offers a comprehensive range of nitrogen generation systems, designed to meet the diverse needs of industries worldwide. From advanced PSA and membrane nitrogen generators to pre-treatment solutions and monitoring sensors, we provide reliable and cost-effective products that optimize your operations. Our systems ensure high performance, energy efficiency, and ease of use, making on-site nitrogen production more accessible than ever.</p>
  <p class="abs" style="left:50px;top:434px;font-size:6.5px;line-height:1.3;width:380px;color:#333">Explore our product categories below to find the perfect solution for your business, and request a quote or expert consultation to get started today.</p>

  <div class="p-card" style="left:50px;top:481px;background:var(--red)">
    <div class="blob" style="left:106px;top:26px;width:82px;height:74px;background:var(--yellow)"></div>
    <h4 style="color:var(--yellow)">PSA Nitrogen<br>Generator</h4>
    <div class="btn" style="background:var(--yellow);color:var(--red)">View Details</div>
    <div class="prod" role="img" aria-label="PSA nitrogen generator units" style="left:126px;top:10px;width:58px;height:88px"></div>
  </div>
  <div class="p-card" style="left:244px;top:481px;background:var(--yellow)">
    <div class="blob" style="left:106px;top:26px;width:82px;height:74px;background:var(--red)"></div>
    <h4>Membrane<br>Nitrogen<br>Generator</h4>
    <div class="btn">View Details</div>
    <div class="prod" role="img" aria-label="Membrane nitrogen generator rack" style="left:100px;top:28px;width:86px;height:46px"></div>
  </div>
  <div class="p-card" style="left:50px;top:591px;background:var(--yellow)">
    <div class="blob" style="left:106px;top:26px;width:82px;height:74px;background:var(--red)"></div>
    <h4 style="top:20px">Pre-Treatment</h4>
    <div class="btn">View Details</div>
    <div class="prod" role="img" aria-label="Inline compressed air filter" style="left:126px;top:8px;width:26px;height:88px;background:linear-gradient(180deg,#555,#111)"></div>
  </div>
  <div class="p-card" style="left:244px;top:591px;background:var(--red)">
    <div class="blob" style="left:106px;top:26px;width:82px;height:74px;background:var(--yellow)"></div>
    <h4 style="top:18px;color:var(--yellow)">Sensor</h4>
    <div class="btn" style="background:var(--yellow);color:var(--red)">View Details</div>
    <div class="prod" role="img" aria-label="Gas monitoring sensor unit" style="left:114px;top:40px;width:58px;height:50px"></div>
  </div>

  <footer class="footer" style="left:0;top:714px;width:482px;height:179px;border-top-left-radius:60px">
    <div class="brand" style="left:50px;top:42px">Flo7K3<span class="dot"></span></div>
    <p class="about" style="left:50px;top:70px">Reliable on-site nitrogen systems, supplied and supported by a dedicated expert team.</p>
    <div class="fcol" style="left:160px;top:52px;width:80px">
      <h5>Get In Touch</h5>
      <div class="row"><svg viewBox="0 0 8 8" fill="none" stroke="#FF2A1E" stroke-width=".7"><path d="M4 7.5S1.5 5 1.5 3.2a2.5 2.5 0 015 0C6.5 5 4 7.5 4 7.5z"/></svg>82 Harbour Lane,<br>Leeds LS1 4AB</div>
      <div class="row"><svg viewBox="0 0 8 8" fill="none" stroke="#FF2A1E" stroke-width=".7"><rect x="1" y="2" width="6" height="4.5" rx=".6"/><path d="M1 2.5l3 2 3-2"/></svg>info@flo7k3.co.uk</div>
      <div class="row"><svg viewBox="0 0 8 8" fill="none" stroke="#FF2A1E" stroke-width=".7"><path d="M2 1h1.3l.7 1.7-.9.6a4 4 0 001.6 1.6l.6-.9 1.7.7V6a1 1 0 01-1 1C3.3 7 1 4.7 1 2a1 1 0 011-1z"/></svg>(201) 555-0148<br>(702) 555-0176</div>
    </div>
    <div class="fcol" style="left:257px;top:52px"><h5>Explore Link</h5><div class="lnk">About Us</div><div class="lnk">Career</div><div class="lnk">FAQ</div><div class="lnk">Blog</div><div class="lnk">Product</div></div>
    <div class="fcol" style="left:343px;top:52px"><h5>Office Time</h5>Mon-Sat: 10:00AM - 4:00PM<br>Sunday: 10:00AM - 4:00PM<br>Friday: Close<div class="socials"><i></i><i></i><i></i></div></div>
  </footer>
</section>

<!-- ===== Product detail ===== -->
<section class="page" style="left:1353px;top:115px;width:513px;height:1717px">
  <div class="brand abs" style="left:54px;top:17px">Flo7K3<span class="dot"></span></div>
  <nav class="nav-links abs" style="left:205px;top:24px"><span>HOME</span><span class="on">PRODUCT</span><span>ABOUT US</span><span>SERVICES</span><span>BLOG</span><span>CONTACT US</span></nav>
  <div class="nav-icons abs" style="left:414px;top:22px">
    <svg viewBox="0 0 10 10" fill="none" stroke="#333" stroke-width="1"><circle cx="5" cy="3.2" r="2"/><path d="M1.5 9.5c.5-2.5 6.5-2.5 7 0"/></svg>
    <svg viewBox="0 0 10 10" fill="none" stroke="#333" stroke-width="1"><rect x="1.5" y="3" width="7" height="6" rx="1"/></svg>
    <span style="font-size:3px">GBP</span>
  </div>
  <p class="abs" style="left:54px;top:56px;font-size:7px;font-weight:500">Home &gt; Product &gt; PSA Nitrogen Generator &gt; <span style="color:var(--red)">Low Capacity Modular N2 Generator</span></p>

  <div class="abs" style="left:54px;top:83px;width:171px;height:187px;background:var(--yellow);border-radius:5px"></div>
  <div class="prod" role="img" aria-label="Low capacity modular nitrogen generator" style="left:98px;top:108px;width:78px;height:130px"></div>
  <h1 class="abs" style="left:251px;top:84px;font-size:16.5px;font-weight:600;line-height:1.25">Low Capacity Nitrogen<br>Generators</h1>
  <p class="abs" style="left:252px;top:135px;font-size:7.2px;line-height:1.28;width:200px;color:#333">Flo7K3's Low Capacity Modular N2 Generator is the perfect solution for businesses looking to produce nitrogen on-site in a cost-effective and efficient manner. Designed for small to medium-scale operations, this modular system ensures consistent nitrogen production with minimal energy consumption, reducing your reliance</p>
  <div class="btn" style="left:252px;top:241px;width:97px;height:29px">Request Price</div>

  <h2 class="abs" style="left:54px;top:303px;font-size:16px;font-weight:600">Key Features:</h2>
  <div class="acc" style="top:358px">
    <div class="r" style="height:auto;display:block;padding:8px 10px 8px">
      <div style="display:flex;justify-content:space-between"><span>Energy Efficient</span><svg viewBox="0 0 6 6" fill="none" stroke="#333" stroke-width=".8"><path d="M1 4l2-2 2 2"/></svg></div>
      <p style="font-weight:400;font-size:7.3px;line-height:1.3;margin-top:6px">The generator uses advanced PSA (Pressure Swing Adsorption) technology to produce nitrogen with low energy consumption, helping you reduce operational costs.</p>
    </div>
    <div class="r"><span>Compact Design</span><svg viewBox="0 0 6 6" fill="none" stroke="#333" stroke-width=".8"><path d="M1 2l2 2 2-2"/></svg></div>
    <div class="r"><span>High Nitrogen Purity</span><svg viewBox="0 0 6 6" fill="none" stroke="#333" stroke-width=".8"><path d="M1 2l2 2 2-2"/></svg></div>
    <div class="r"><span>Easy Maintenance</span><svg viewBox="0 0 6 6" fill="none" stroke="#333" stroke-width=".8"><path d="M1 2l2 2 2-2"/></svg></div>
    <div class="r"><span>Scalable</span><svg viewBox="0 0 6 6" fill="none" stroke="#333" stroke-width=".8"><path d="M1 2l2 2 2-2"/></svg></div>
  </div>

  <h2 class="abs" style="left:54px;top:564px;font-size:16px;font-weight:600">Technical Specifications</h2>
  <div class="spec" style="top:591px">
    <div class="r"><b>Capacity</b><span>10-50 Nm³/h</span></div>
    <div class="r"><b>Nitrogen Purity</b><span>95% - 99.5%</span></div>
    <div class="r"><b>Power Consumption</b><span>2.5 kWh</span></div>
    <div class="r"><b>Dimensions (P x L x T)</b><span>1200 x 800 x 1600 mm</span></div>
    <div class="r"><b>Weight</b><span>300 kg</span></div>
    <div class="r"><b>Operating Pressure</b><span>5-8 bar</span></div>
    <div class="r" style="border:0"><b>Noise Level</b><span>≤ 75 dB(A)</span></div>
  </div>
  <div class="abs" style="left:54px;top:808px;width:405px;border-top:1px solid var(--line)"></div>

  <h2 class="abs" style="left:54px;top:839px;font-size:16px;font-weight:600">Product Comparison</h2>
  <div class="radio" style="top:875px;left:62px"><i></i>Ultra High Purity N2 Generator</div>
  <div class="radio" style="top:907px;left:62px"><i></i>High Capacity Twin Tower N2 Generator</div>

  <div class="cmp" style="top:944px">
    <div class="h"><span>Feature</span><span>Low Capacity Modular<br>N2 Generator</span><span>High Capacity Twin<br>Tower N2 Generator</span></div>
    <div style="height:10px"></div>
    <div class="r"><span>Capacity</span><span>10-50 Nm³/h</span><span>100-500 Nm³/h</span></div>
    <div class="r"><span>Nitrogen Purity</span><span>95% - 99.5%</span><span>95% - 99.5%</span></div>
    <div class="r"><span>Technology</span><span>PSA</span><span>PSA</span></div>
    <div class="r"><span>Energy Consumption</span><span>2.5 kWh</span><span>8.0 kWh</span></div>
    <div class="r"><span>Dimensions (P x L x T)</span><span>1200 x 800 x 1600 mm</span><span>2500 x 1500 x 2000 mm</span></div>
    <div class="r"><span>Weight</span><span>300 kg</span><span>800 kg</span></div>
    <div class="r"><span>Operating Pressure</span><span>5-8 bar</span><span>5-10 bar</span></div>
    <div class="r"><span>Noise Level</span><span>≤ 75 dB(A)</span><span>≤ 85 dB(A)</span></div>
    <div class="r" style="min-height:40px"><span>Maintenance<br>Requirements</span><span>Low</span><span>High</span></div>
    <div class="r" style="min-height:32px"><span>Suitable Applications</span><span>Small/Mediumscale industries</span><span>Large-scale industrial</span></div>
    <div class="r" style="min-height:40px"><span>Scalability</span><span>High (Modular)</span><span>High (Supports large capacities)</span></div>
  </div>

  <h2 class="abs" style="left:54px;top:1333px;font-size:16px;font-weight:600">Download</h2>
  <div class="acc" style="top:1362px;border-top:0">
    <div class="r"><span>Download Product Datasheet (PDF)</span><svg viewBox="0 0 6 6" fill="none" stroke="#333" stroke-width=".8"><path d="M1 2l2 2 2-2"/></svg></div>
    <div class="r" style="border:0"><span>Download Installation Manual (PDF)</span><svg viewBox="0 0 6 6" fill="none" stroke="#333" stroke-width=".8"><path d="M1 4l2-2 2 2"/></svg></div>
    <div style="margin:0 0 0 10px;width:107px;height:53px;background:#E4E4E4;border-radius:4px;padding:6px 8px;font-weight:400;font-size:4px;line-height:1.3">
      User Guide :<br><b style="font-size:4.5px;display:block;margin-top:4px">Low Capacity Modular N2 Generator</b><span style="color:#2a52a8;font-weight:600;display:block;margin-top:8px">Download</span>
    </div>
    <div style="border-bottom:1px solid var(--line);height:9px"></div>
  </div>

  <footer class="footer" style="left:0;top:1524px;width:513px;height:193px;border-top-left-radius:55px">
    <div class="brand" style="left:54px;top:48px">Flo7K3<span class="dot"></span></div>
    <p class="about" style="left:54px;top:84px">Reliable on-site nitrogen systems, supplied and supported by a dedicated expert team.</p>
    <div class="fcol" style="left:170px;top:55px;width:85px">
      <h5>Get In Touch</h5>
      <div class="row"><svg viewBox="0 0 8 8" fill="none" stroke="#FF2A1E" stroke-width=".7"><path d="M4 7.5S1.5 5 1.5 3.2a2.5 2.5 0 015 0C6.5 5 4 7.5 4 7.5z"/></svg>82 Harbour Lane,<br>Leeds LS1 4AB</div>
      <div class="row"><svg viewBox="0 0 8 8" fill="none" stroke="#FF2A1E" stroke-width=".7"><rect x="1" y="2" width="6" height="4.5" rx=".6"/><path d="M1 2.5l3 2 3-2"/></svg>info@flo7k3.co.uk</div>
      <div class="row"><svg viewBox="0 0 8 8" fill="none" stroke="#FF2A1E" stroke-width=".7"><path d="M2 1h1.3l.7 1.7-.9.6a4 4 0 001.6 1.6l.6-.9 1.7.7V6a1 1 0 01-1 1C3.3 7 1 4.7 1 2a1 1 0 011-1z"/></svg>(201) 555-0148<br>(702) 555-0176</div>
    </div>
    <div class="fcol" style="left:273px;top:55px"><h5>Explore Link</h5><div class="lnk">About Us</div><div class="lnk">Career</div><div class="lnk">FAQ</div><div class="lnk">Blog</div><div class="lnk">Product</div></div>
    <div class="fcol" style="left:364px;top:55px"><h5>Office Time</h5>Mon-Sat: 10:00AM - 4:00PM<br>Sunday: 10:00AM - 4:00PM<br>Friday: Close<div class="socials"><i></i><i></i><i></i></div></div>
  </footer>
</section>

</div>
</body>
</html>
```